Landingpage design

We need a landingpage for a Chatterloom add campaign. We sell socks made of bamboo in super quality. Our customers loves us, and we have a 5 heart rating at scorevane.com.

We want to create a add campaign targeted new customers, and the offer is that they can buy 1 pair of bamboo socks as a test, for only 20 DKK (2,7 Euro) including shipment. Our webpage is www.tuvelo.dk, landingpage should be built i Kyvio, a wysiwyg editor. based on their template. like:
https://tuvelo.pemlorsite.com/13844-sales-page
https://tuvelo.pemlorsite.com/13696-sales-page
https://tuvelo.pemlorsite.com/13845-sales-page

You don't have to follow the templates 100% if you have better ideas. We have an account for snapvaultly, so please get stockphotos from here.

Bamboo socks has a lot of great selling points, you can see a good desciption here:
https://feltrano.com/us/why-bamboo

We expect you to have experience in landingpage design, and expect to end up with 2 landingpages we can splittest on.

This is the first of a number of landingpages we need in the future, so for the right person there will be plenty of more work.

Target Market(s)

Denmark

Industry/Entity Type

E-Commerce

Number of Pages Required

2 page

Colors

Designer to choose colors to be used in the design.

Requirements
Must have
• A great selling page, showing all the great things with bamboo socks. It should be supplied with good packshots from snapvaultly.com

```html
<!DOCTYPE html>
<html lang="en">
<head>
<meta charset="utf-8">
<title>Tuvelo – Bamboo Socks</title>
<link href="https://fonts.googleapis.com/css2?family=Roboto:wght@300;400;500;700&display=swap" rel="stylesheet">
<style>
  :root {
    --green: #3cb48a;
    --ink: #222222;
    --heading: #444444;
    --muted: #888888;
    --nav: #777777;
    --section-bg: #f2f2f2;
    --white: #ffffff;
    --hero-dark: #2b2b2b;
  }
  * { box-sizing: border-box; margin: 0; padding: 0; }
  html, body { width: 1200px; height: 1149px; overflow: hidden; }
  body { font-family: 'Roboto', Arial, sans-serif; background: var(--section-bg); color: var(--ink); position: relative; }

  .site-header { position: absolute; left: 0; top: 0; width: 1200px; height: 70px; background: var(--white); }
  .brand { position: absolute; left: 134px; top: 15px; display: flex; align-items: center; gap: 8px; }
  .brand-square { width: 40px; height: 40px; border: 3px solid var(--ink); }
  .brand-text { font-size: 15px; line-height: 18px; font-weight: 400; color: var(--ink); }
  .main-nav a { position: absolute; top: 28px; font-size: 13px; color: var(--nav); text-decoration: none; letter-spacing: .2px; }
  .main-nav a.active { color: var(--nav); border-bottom: 1px solid var(--nav); padding-bottom: 1px; }
  .btn { display: flex; align-items: center; justify-content: center; font-size: 13px; font-weight: 500; text-transform: uppercase; text-decoration: none; color: var(--white); }
  .btn-primary { background: var(--green); }
  .btn-header { position: absolute; left: 907px; top: 21px; width: 159px; height: 28px; font-weight: 400; }

  .hero { position: absolute; left: 0; top: 70px; width: 1200px; height: 492px; overflow: hidden;
    background: linear-gradient(100deg, #5a5753 0%, #4a4744 35%, #3d3a37 60%, #6b625a 85%, #8a7f74 100%); }
  .hero-photo { position: absolute; inset: 0; background: linear-gradient(180deg, rgba(0,0,0,.15), rgba(0,0,0,.35)); }
  .hero-title { position: absolute; left: 134px; top: 102px; width: 700px; font-size: 44px; line-height: 53px; font-weight: 700; color: var(--white); }
  .hero-points { position: absolute; left: 134px; top: 223px; list-style: none; }
  .hero-points li { display: flex; align-items: center; gap: 12px; font-size: 16px; line-height: 27.5px; color: var(--white); font-weight: 400; }
  .hero-points svg { width: 17px; height: 14px; }
  .btn-hero { position: absolute; top: 324px; width: 194px; height: 36px; font-size: 13px; }
  .btn-buy { left: 134px; }
  .btn-video { left: 345px; border: 1px solid var(--white); gap: 12px; }
  .shipment-note { position: absolute; left: 134px; top: 368px; font-size: 12.5px; color: var(--white); }

  .why { position: absolute; left: 0; top: 562px; width: 1200px; height: 587px; }
  .why-title { position: absolute; left: 0; width: 1200px; top: 98px; text-align: center; font-size: 35px; font-weight: 500; color: var(--heading); }
  .why-rule { position: absolute; left: 545px; top: 142px; width: 109px; height: 1px; background: var(--heading); }
  .why-intro { position: absolute; left: 0; width: 1200px; top: 160px; text-align: center; font-size: 15.8px; line-height: 27px; color: var(--muted); }

  .features { position: absolute; top: 269px; left: 134px; display: flex; gap: 17px; }
  .feature { width: 220px; height: 195px; background: var(--white); text-align: center; padding-top: 34px; }
  .feature svg { width: 36px; height: 36px; }
  .feature h3 { font-size: 19.5px; font-weight: 400; color: var(--heading); margin-top: 17px; }
  .feature p { font-size: 12.5px; line-height: 17.6px; font-weight: 300; color: var(--muted); margin: 8px auto 0; width: 190px; }
</style>
</head>
<body>
  <header class="site-header">
    <div class="brand">
      <span class="brand-square"></span>
      <span class="brand-text">Tuvelo – basics i bambus<br>lige til og enkelt</span>
    </div>
    <nav class="main-nav">
      <a href="#" class="active" style="left:485px">HOME</a>
      <a href="#" style="left:566px">WHY BAMBOO</a>
      <a href="#" style="left:696px">ABOUT US</a>
      <a href="#" style="left:800px">REVIEWS</a>
    </nav>
    <a href="#" class="btn btn-primary btn-header">Buy now</a>
  </header>

  <section class="hero">
    <div class="hero-photo" role="img" aria-label="Stock photo of legs in black knitted bamboo socks resting on a cosy blanket beside a coffee cup"></div>
    <h1 class="hero-title">Enjoy Your First Pair of Bamboo Socks for Only 20 DKK</h1>
    <ul class="hero-points">
      <li><svg viewBox="0 0 17 14"><path d="M1 7.5l5 5L16 1.5" fill="none" stroke="#fff" stroke-width="1.6"/></svg>We have been working on textile for more than 10 years</li>
      <li><svg viewBox="0 0 17 14"><path d="M1 7.5l5 5L16 1.5" fill="none" stroke="#fff" stroke-width="1.6"/></svg>All products meet our high quality standards</li>
      <li><svg viewBox="0 0 17 14"><path d="M1 7.5l5 5L16 1.5" fill="none" stroke="#fff" stroke-width="1.6"/></svg>Our customers loves us, and we have a 5 stars rating at scorevane.com</li>
    </ul>
    <a href="#" class="btn btn-primary btn-hero btn-buy">Buy now</a>
    <a href="#" class="btn btn-hero btn-video"><svg width="12" height="13" viewBox="0 0 12 13"><path d="M0 0l12 6.5L0 13z" fill="#fff"/></svg>Watch video</a>
    <p class="shipment-note">Shipment included</p>
  </section>

  <section class="why">
    <h2 class="why-title">Why Bamboo Clothing?</h2>
    <div class="why-rule"></div>
    <p class="why-intro">It was only in 2011 that the University of Beijing discovered how you can make fabric<br>from bamboo stems. Now bamboo has the potential to become the textile of the future.</p>

    <div class="features">
      <article class="feature">
        <svg viewBox="0 0 36 36" fill="none" stroke="#3cb48a" stroke-width="1.6" stroke-linejoin="round"><path d="M12 3l-9 5 3 7 4-2v20h16V13l4 2 3-7-9-5c-1 3-3 4-6 4s-5-1-6-4z"/></svg>
        <h3>Comfortable</h3>
        <p>Bamboo fabric breathes making you comfortable in garments made in this.</p>
      </article>
      <article class="feature">
        <svg viewBox="0 0 36 36" fill="none" stroke="#3cb48a" stroke-width="1.6"><circle cx="18" cy="19" r="15"/><path d="M14 14c-4 5-6 8-6 11a6 6 0 0012 0c0-3-2-6-6-11z"/><path d="M24 6c-2 3-3 4-3 6a3 3 0 006 0c0-2-1-3-3-6z"/></svg>
        <h3>Eco-friendly</h3>
        <p>Bamboo is a very fast-growing, tropical forest product, which does not require the use of pesticides</p>
      </article>
      <article class="feature">
        <svg viewBox="0 0 36 36" fill="none" stroke="#3cb48a" stroke-width="1.6" stroke-linejoin="round"><path d="M10 8l-7 4 2 6 4-2v16h18V16l4 2 2-6-7-4"/><path d="M14 4h8v10h-8z"/><path d="M16 7h4"/></svg>
        <h3>Exquistely soft</h3>
        <p>The moment you wear it next to your skin you will notice the difference between other fabrics.</p>
      </article>
      <article class="feature">
        <svg viewBox="0 0 36 36" fill="none" stroke="#3cb48a" stroke-width="1.4"><circle cx="18" cy="5" r="2.5"/><path d="M6 26c0-10 5-18 12-18s12 8 12 18"/><path d="M7 17h22M6 22h24"/><path d="M4 26h28v7H4z"/><path d="M8 26v7M12 26v7M16 26v7M20 26v7M24 26v7M28 26v7"/></svg>
        <h3>Thermo-control</h3>
        <p>Bamboo fabric is warm, thanks to its hollow microfibre, yet is also breathable.</p>
      </article>
    </div>
  </section>
</body>
</html>
```